Bramble Hockey Academy

We are are Ice Hockey Development Company that provided on-ice Hockey development services. We need a Landing Page with tabs to direct to individual program pages.
Landing Page
About Page
Winter Program Page
Spring Program Page
Summer Program Page
Team Page
Tournament Page

Coded - Design and coding required

5+ page

```html
<!DOCTYPE html>
<html lang="en">
<head>
<meta charset="utf-8">
<title>Bramble Hockey Academy</title>
<link href="https://fonts.googleapis.com/css2?family=Montserrat:wght@400;500;600;700;800&family=Mulish:wght@400&display=swap" rel="stylesheet">
<style>
  :root {
    --green: #1e8a24;
    --ink: #111111;
    --text: #2a2a2a;
    --white: #ffffff;
    --navy: #1c2640;
    --ice: #dfe8ee;
    --line: #333333;
  }
  * { margin: 0; padding: 0; box-sizing: border-box; }
  html, body { width: 724px; height: 1200px; overflow: hidden; background: var(--white); }
  body { position: relative; font-family: 'Mulish', sans-serif; color: var(--text); }
  .abs { position: absolute; }
  .heading-font { font-family: 'Montserrat', sans-serif; }

  /* Hero */
  .hero { left: 0; top: 0; width: 724px; height: 400px; overflow: hidden; }
  .hero-photo {
    position: absolute; inset: 0;
    background:
      radial-gradient(ellipse 220px 120px at 280px 60px, rgba(255,220,170,.55), transparent 70%),
      linear-gradient(180deg, #1a2238 0%, #3a4766 35%, #5d6a85 58%, #bfcfd8 72%, #e4ecef 100%);
  }
  .brand { font-family: 'Montserrat', sans-serif; font-weight: 800; line-height: 1; letter-spacing: .3px; }
  .hero .brand { left: 79px; top: 13px; color: var(--white); font-size: 13px; }
  .main-nav { top: 20px; left: 325px; height: 16px; display: flex; align-items: center;
    font-family: 'Montserrat', sans-serif; font-weight: 700; font-size: 8.4px; color: var(--white); }
  .main-nav span { position: absolute; white-space: nowrap; }
  .main-nav .active { background: var(--green); padding: 4px 5px; top: 0; }
  .chev { display: inline-block; vertical-align: middle; margin-left: 4px; }
  .hero-title { left: 427px; top: 127px; color: var(--white); font-family: 'Montserrat', sans-serif; font-weight: 700; }
  .hero-title .kicker { font-size: 15.5px; letter-spacing: .3px; }
  .hero-title .name { font-size: 23px; font-weight: 800; margin-top: 6px; }
  .btn { display: inline-flex; align-items: center; justify-content: center; background: var(--green);
    color: var(--white); font-family: 'Montserrat', sans-serif; font-weight: 700; }
  .btn-lg { left: 427px; top: 191px; width: 76px; height: 25px; font-size: 8.4px; }
  .btn-sm { width: 53px; height: 17px; font-size: 5.6px; }
  .dots { left: 346px; top: 379px; display: flex; gap: 3px; }
  .dots i { width: 4px; height: 4px; border-radius: 50%; background: #1a1a1a; display: block; }
  .dots i.on { background: var(--green); }

  /* Welcome */
  .section-title { font-family: 'Montserrat', sans-serif; font-weight: 700; font-size: 12.5px; color: var(--ink); }
  .rule { height: 1.5px; background: var(--green); }
  .welcome-title { left: 80px; top: 438px; }
  .welcome-rule { left: 80px; top: 464px; width: 72px; }
  .welcome-copy { left: 81px; top: 484px; width: 218px; font-size: 8px; line-height: 12.6px; text-align: justify; }
  .welcome-btn { left: 82px; top: 605px; }
  .welcome-photo { left: 312px; top: 424px; width: 355px; height: 233px;
    background: radial-gradient(ellipse at center, #c9d6df 0%, #e6edf1 55%, #ffffff 100%); }

  /* Programs */
  .programs { left: 0; top: 669px; width: 724px; height: 435px;
    background: linear-gradient(90deg, #e9edf2 0%, #f1f3f6 60%, #f6f6f8 100%); }
  .programs-photo { left: 0; top: 669px; width: 360px; height: 435px;
    background: linear-gradient(160deg, #c6ccd6 0%, #6c7891 35%, #b54a52 55%, #c8d0d8 80%, #e6eaee 100%); }
  .programs-title { left: 391px; top: 693px; }
  .programs-rule { left: 391px; top: 717px; width: 29px; }
  .program-thumb { left: 375px; width: 83px; height: 82px; border-radius: 44% 44% 46% 46%; }
  .program-name { left: 472px; font-family: 'Montserrat', sans-serif; font-weight: 700; font-size: 8.4px; color: var(--ink); white-space: pre; }
  .program-copy { left: 472px; width: 170px; font-family: 'Montserrat', sans-serif; font-size: 7.2px; line-height: 10.2px; color: var(--text); }
  .program-btn { left: 473px; }

  /* Footer */
  .footer .brand { left: 79px; top: 1130px; color: var(--ink); font-size: 14px; }
  .footer-nav { top: 1136px; font-family: 'Montserrat', sans-serif; font-weight: 500; font-size: 8.4px; color: var(--ink); }
  .footer-rule { left: 352px; top: 1155px; width: 293px; height: 1px; background: var(--line); }
  .copyright { right: 79px; top: 1166px; font-size: 7px; color: #444; }
</style>
</head>
<body>

<header class="hero abs">
  <div class="hero-photo" role="img" aria-label="Ice hockey players skating after the puck in a brightly lit arena"></div>
  <div class="brand abs">BRAMBLE<br>HOCKEY<br>ACADEMY</div>
  <nav class="main-nav abs">
    <span class="active" style="left:0">HOME</span>
    <span style="left:50px">ABOUT</span>
    <span style="left:102px">OUR PROGRAMS<svg class="chev" width="8" height="6" viewBox="0 0 8 6"><path d="M1 1l3 3.5L7 1" fill="none" stroke="#fff" stroke-width="1.4"/></svg></span>
    <span style="left:209px">TEAM</span>
    <span style="left:257px">TOURNAMENT</span>
  </nav>
  <div class="hero-title abs">
    <div class="kicker">WELCOME TO</div>
    <div class="name">BRAMBLE HOCKEY</div>
  </div>
  <a class="btn btn-lg abs">READ MORE</a>
  <div class="dots abs"><i></i><i></i><i class="on"></i><i></i><i></i></div>
</header>

<section class="welcome">
  <h2 class="section-title welcome-title abs">WELCOME TO BRAMBLE HOCKEY</h2>
  <div class="rule welcome-rule abs"></div>
  <p class="welcome-copy abs">There are many variations of passages of Lorem Ipsum available, but the majority have suffered alteration in some form, by injected humour, or randomised words which don't look even slightly believable. If you are going to use a passage of Lorem Ipsum, you need to be sure there isn't anything embarrassing hidden in the middle of text. All the Lorem Ipsum generators on the Internet tend to repeat predefined chunks as necessary</p>
  <a class="btn btn-sm welcome-btn abs">READ MORE</a>
  <div class="welcome-photo abs" role="img" aria-label="Two hockey players competing for the puck on white ice"></div>
</section>

<section>
  <div class="programs abs"></div>
  <div class="programs-photo abs" role="img" aria-label="Hockey player in red stickhandling, blended with a city skyline montage"></div>
  <h2 class="section-title programs-title abs">OUR PROGRAMS</h2>
  <div class="rule programs-rule abs"></div>

  <div class="program-thumb abs" style="top:746px;background:linear-gradient(180deg,#2b3547,#7d8ba0 55%,#dfe7ec)" role="img" aria-label="Players skating during winter training"></div>
  <h3 class="program-name abs" style="top:745px">WINTER PROGRAM</h3>
  <p class="program-copy abs" style="top:760px">There are many variations of passages of Lorem Ipsum available, but the majority have suffered alteration in some form, by injected humour, or randomised words which.</p>
  <a class="btn btn-sm program-btn abs" style="top:810px">READ MORE</a>

  <div class="program-thumb abs" style="top:860px;background:linear-gradient(180deg,#8c4a45,#c7343a 45%,#d9dde2)" role="img" aria-label="Two young players battling for the puck"></div>
  <h3 class="program-name abs" style="top:859px">SPRING PROGRAM</h3>
  <p class="program-copy abs" style="top:874px">There are many variations of passages of Lorem Ipsum available, but the majority have suffered alteration in some form, by injected humour, or randomised words which.</p>
  <a class="btn btn-sm program-btn abs" style="top:924px">READ MORE</a>

  <div class="program-thumb abs" style="top:987px;background:linear-gradient(180deg,#4a3a30,#8c7464 40%,#c94a45 60%,#e3e6ea)" role="img" aria-label="Young player in red skating with the puck in an indoor rink"></div>
  <h3 class="program-name abs" style="top:986px">SUMMER  PROGRAM</h3>
  <p class="program-copy abs" style="top:1001px">There are many variations of passages of Lorem Ipsum available, but the majority have suffered alteration in some form, by injected humour, or randomised words which.</p>
  <a class="btn btn-sm program-btn abs" style="top:1051px">READ MORE</a>
</section>

<footer class="footer">
  <div class="brand abs">BRAMBLE<br>HOCKEY<br>ACADEMY</div>
  <span class="footer-nav abs" style="left:351px">HOME</span>
  <span class="footer-nav abs" style="left:395px">ABOUT</span>
  <span class="footer-nav abs" style="left:446px">OUR PROGRAMS</span>
  <span class="footer-nav abs" style="left:537px">TEAM</span>
  <span class="footer-nav abs" style="left:583px">TOURNAMENT</span>
  <div class="footer-rule abs"></div>
  <p class="copyright abs">Copyright © 2023 All Rights Reserved</p>
</footer>

</body>
</html>
```